Custom Wordpress Theme - Original and Professional

We are a boutique IT consulting firm that provide small and medium business in Australia three different levels of IT service.
We are looking for a developer who will create a customised, original and professional wordpress theme. We are looking for the developer to create a professional, clean, clear and simple theme with a stylish layout, images and icons.
Our three services are: IT support | IT Services | IT Solutions and we would like to clearly differentiate the difference in each level of service in as few words as possible.
IT Support is the ad hock “call us, when you need us” service, that smaller business or those with minimal issues use.
IT service is the unlimited service, that business with existing (and well maintained) IT systems choose and is both flexible and scalable including no contracts or paperwork required.
IT solutions are the unlimited service that businesses that need new or updated infrastructure choose and it includes all the hardware, software and services with no contracts or any ongoing commitment.
The main page on the web site will attract the visitor to choose the right “service level” for their business and then we will have a dedicated page for each service and another page for a comparison (table) to compare all three services.
Lastly we will need a contact us page that has both office locations (Sydney and Melbourne), contact phone numbers and an email form.
Items we are focused on for this project are: 1. Images, 2.Icons 3. Layout.
In summary we are looking for a custom WordPress theme into a 6 page (Home, IT Support, IT Services, IT Solutions, Compare Service levels and Contact us) website. The design must include relevant images and icons and be clear, simple, professional and sleek.

Thank you for your time and creativity and I look forward to working with you!

Target Market(s)

Small and Medium businesses in Australia

Industry/Entity Type

Boutique

Requirements
Must have
• - 6 Pages layout: Home, IT support, IT services, IT Solutions, Compare service levels and Contact us
- Images, Layout and Icons.
- Clean, Clear, Simple, Elegant, Stylish.
Nice to have
• - Some text (if possible but not required).
Should not have
• - Complexity.
- Confusing layout.
- Generic non matching images and icons.

```html
<!DOCTYPE html>
<html lang="en">
<head>
<meta charset="utf-8">
<title>Contact Us</title>
<link href="https://fonts.googleapis.com/css2?family=Marcellus&family=Noto+Sans:wght@400;700&family=Ubuntu+Condensed&display=swap" rel="stylesheet">
<style>
  :root{
    --accent:#3ddfe3;
    --ink:#1c1c1c;
    --muted:#8a8a8a;
    --field:#f0f0f0;
    --field-edge:#dcdcdc;
    --map-light:#e8e5da;
    --map-mid:#d9dec8;
    --white:#ffffff;
  }
  *{box-sizing:border-box;margin:0;padding:0}
  html,body{width:840px;height:1200px;overflow:hidden;background:var(--white)}
  body{position:relative;font-family:"Noto Sans",sans-serif;color:var(--ink);font-size:12px}
  .abs{position:absolute}
  .brand{left:45px;top:56px;font-family:"Marcellus",serif;font-size:21px;font-weight:400;letter-spacing:.3px}
  .tagline{left:64px;top:84px;font-size:7.5px;color:var(--muted);letter-spacing:.2px}
  .nav{left:360px;top:64px;display:flex;gap:16px;font-size:12px}
  .nav a{color:var(--ink);text-decoration:none}
  .nav a.current{color:var(--accent)}
  .page-title{left:50px;top:145px;font-family:"Marcellus",serif;font-size:13px;font-weight:400}
  .crumbs{left:51px;top:165px;font-size:6.5px;font-style:italic}
  .crumbs span{color:var(--accent)}
  .map{left:97px;top:224px;width:611px;height:253px;
    background:linear-gradient(90deg,var(--map-light) 0%,var(--map-light) 50%,var(--map-mid) 100%)}
  .section-head{font-family:"Marcellus",serif;font-size:14px;font-weight:400;top:530px}
  .rule{height:1.5px;background:var(--accent);top:558px}
  .label{font-size:11px}
  .field{background:var(--field);border:1px solid var(--field-edge);border-left:1.5px solid #b5b5b5}
  .btn{top:916px;height:30px;border:1px solid #cfcfcf;border-radius:8px;background:linear-gradient(#fafafa,#e6e6e6);
    font-family:"Ubuntu Condensed",sans-serif;font-size:10px;display:flex;align-items:center;justify-content:center;box-shadow:0 1px 2px rgba(0,0,0,.15)}
  .info{font-size:11.5px;line-height:20px}
  .info .link{color:var(--accent)}
  .addr-head{font-size:11.5px;left:528px}
  .icon-box{left:525px;width:24px;height:33px;background:#d6d6d6;border:1px solid #c4c4c4;display:flex;align-items:center;justify-content:center}
  .icon-text{left:555px;font-size:11px}
  .icon-text .small{font-size:9.5px}
  .footer{left:0;top:1153px;width:840px;height:47px;background:var(--accent);color:var(--white)}
  .footer .copy{position:absolute;left:53px;top:15px;font-size:12px}
  .footer .social{position:absolute;right:38px;top:19px;display:flex;gap:4px}
  .footer .social i{display:block;width:7px;height:7px;background:var(--white)}
</style>
</head>
<body>
  <header>
    <div class="abs brand">COMPANY NAME</div>
    <div class="abs tagline">YOUR COMPANY SOLGAN</div>
    <nav class="abs nav">
      <a href="#">Home</a><a href="#">IT support</a><a href="#">IT Services</a><a href="#">IT Solutions</a><a href="#">Service</a><a href="#" class="current">Contact us</a>
    </nav>
  </header>

  <h1 class="abs page-title">CONTACT US</h1>
  <div class="abs crumbs">HOME | <span>CONTACT US</span></div>

  <div class="abs map" role="img" aria-label="Street map showing the Melbourne office location"></div>

  <h2 class="abs section-head" style="left:45px">QUERY FORM</h2>
  <div class="abs rule" style="left:47px;width:458px"></div>
  <h2 class="abs section-head" style="left:527px">CONTACT INFORMATION</h2>
  <div class="abs rule" style="left:527px;width:242px"></div>

  <form class="query-form">
    <label class="abs label" style="left:45px;top:602px">FIRST NAME</label>
    <div class="abs field" style="left:45px;top:627px;width:220px;height:41px"></div>
    <label class="abs label" style="left:284px;top:602px">LAST NAME</label>
    <div class="abs field" style="left:283px;top:627px;width:220px;height:41px"></div>
    <label class="abs label" style="left:46px;top:677px">PHONE NUMBER</label>
    <div class="abs field" style="left:45px;top:702px;width:220px;height:48px"></div>
    <label class="abs label" style="left:286px;top:677px">E-MAIL</label>
    <div class="abs field" style="left:283px;top:702px;width:220px;height:41px"></div>
    <label class="abs label" style="left:54px;top:775px">MESSAGE</label>
    <div class="abs field" style="left:45px;top:795px;width:458px;height:76px"></div>
    <svg class="abs" style="left:211px;top:937px" width="8" height="12" viewBox="0 0 8 12"><path d="M6 1 L2 6 L6 11" fill="none" stroke="#3ddfe3" stroke-width="1.3"/></svg>
    <div class="abs btn" style="left:337px;width:54px">CLEAR</div>
    <div class="abs btn" style="left:400px;width:49px">SEND</div>
  </form>

  <section class="contact-info">
    <div class="abs addr-head" style="top:580px">ADDRRESS 1</div>
    <div class="abs info" style="left:523px;top:607px">P.O.BOX : 40215<br>MELBOURNE,<br>AUSTRALIA</div>
    <div class="abs info" style="left:654px;top:607px">PHONE : +61 3 9012 4478<br>FAX : +61 2 9384 1150<br>EMAIL : <span class="link">info@bayline-it.com</span></div>
    <div class="abs addr-head" style="top:680px">ADDRRESS 2</div>
    <div class="abs info" style="left:523px;top:708px">P.O.BOX : 40215<br>Sydney,<br>AUSTRALIA</div>
    <div class="abs info" style="left:654px;top:708px">PHONE : +61 3 9012 4478<br>FAX : +61 2 9384 1150<br>EMAIL : <span class="link">info@bayline-it.com</span></div>

    <div class="abs icon-box" style="top:819px"><svg width="10" height="16" viewBox="0 0 10 16"><rect x="1" y="1" width="8" height="14" rx="1.5" fill="none" stroke="#fff" stroke-width="1.2"/><rect x="3" y="3" width="4" height="6" fill="#fff"/></svg></div>
    <div class="abs icon-text" style="top:827px"><span class="small">PHONE :</span> +61 3 9012 4478</div>
    <div class="abs icon-box" style="top:871px"><svg width="14" height="10" viewBox="0 0 14 10"><rect x="1" y="1" width="12" height="8" fill="none" stroke="#fff" stroke-width="1.2"/><path d="M1 1 L7 6 L13 1" fill="none" stroke="#fff" stroke-width="1.2"/></svg></div>
    <div class="abs icon-text" style="top:879px"><span class="small">EMAIL :</span> <span style="color:var(--accent)">info@bayline-it.com</span></div>
    <div class="abs icon-box" style="top:923px"><svg width="10" height="10" viewBox="0 0 10 10"><rect x="1" y="1" width="8" height="8" fill="#fff"/></svg></div>
    <div class="abs icon-text" style="top:930px"><span class="small">FACEBOOK :</span> baylineit</div>
  </section>

  <footer class="abs footer">
    <div class="copy">IT SOLUTION© 2013 • Privacy Policy</div>
    <div class="social"><i></i><i></i><i></i><i></i></div>
  </footer>
</body>
</html>
```